Redesign of business card for Cedar Ridge Mechanical

We are looking for a new design for our business cards for Cedar Ridge Mechanical. We are a plumbing & HVAC construction company, operating on the West Coast of Canada and USA. Logo attached.
Industry/Entity Type
Construction - Plumbing & HVAC
Contact Information for Business Card
Name, address, phone numbers, email, website address
Look and feel
Each slider illustrates characteristics of the customer's brand and the style your logo design should communicate.

```html
<!DOCTYPE html>
<html lang="en">
<head>
<meta charset="UTF-8">
<title>Cedar Ridge Mechanical – Business Card</title>
<link href="https://fonts.googleapis.com/css2?family=Poppins:wght@300;400;600;700&display=swap" rel="stylesheet">
<style>
  :root {
    --stage: #262626;
    --card: #222222;
    --card-back: #1f2022;
    --ink: #ffffff;
    --muted: #d9d9d9;
    --rule: #8a8a8a;
  }
  * { box-sizing: border-box; margin: 0; padding: 0; }
  html, body {
    width: 1200px; height: 780px; overflow: hidden;
    background: var(--stage);
    font-family: "Poppins", sans-serif;
    color: var(--ink);
  }
  .stage {
    width: 1200px; height: 780px;
    display: flex; align-items: center; justify-content: center; gap: 40px;
  }
  .card {
    position: relative;
    width: 540px; height: 309px;
    overflow: hidden;
    box-shadow: 0 14px 30px rgba(0,0,0,.45);
  }
  .card--front { background: var(--card); }
  .card--back { background: var(--card-back); }

  .edge-bar { position: absolute; width: 11px; background: var(--ink); }
  .edge-bar--left { left: 0; top: 168px; bottom: 0; }
  .edge-bar--right { right: 0; top: 0; height: 132px; }

  .brand {
    position: absolute; left: 40px; top: 58px; width: 220px;
    display: flex; align-items: center; gap: 12px;
  }
  .brand__square {
    flex: none; width: 46px; height: 46px;
    background: var(--ink); border-radius: 6px;
  }
  .brand__name {
    font-weight: 600; font-size: 19px; line-height: 1.2;
    letter-spacing: .5px; text-transform: uppercase; color: var(--ink);
  }

  .divider {
    position: absolute; left: 292px; top: 52px; width: 1px; height: 150px;
    background: linear-gradient(to bottom, transparent, var(--rule) 40%, var(--rule) 60%, transparent);
  }

  .contact { position: absolute; left: 318px; top: 44px; width: 210px; }
  .contact__name { font-size: 25px; line-height: 1.1; white-space: nowrap; }
  .contact__first { font-weight: 700; }
  .contact__last { font-weight: 300; }
  .contact__title { font-size: 12.5px; font-weight: 400; margin-top: 2px; }
  .contact__list { list-style: none; margin-top: 18px; }
  .contact__item {
    display: flex; align-items: center; gap: 8px;
    font-size: 12.5px; font-weight: 400; line-height: 1.75; white-space: nowrap;
  }
  .contact__item svg { width: 12px; height: 12px; flex: none; }

  .address {
    position: absolute; left: 36px; right: 30px; bottom: 30px;
    font-size: 15.5px; font-weight: 400; letter-spacing: .3px; white-space: nowrap;
  }

  .pattern {
    position: absolute; inset: 0;
    background: linear-gradient(200deg, #3a3b3e 0%, #2a2b2e 35%, #1e1f21 70%, #1b1c1e 100%);
  }
  .back-brand {
    position: absolute; left: 330px; top: 170px;
    display: flex; align-items: center; gap: 6px;
  }
  .back-brand__square { width: 16px; height: 16px; background: var(--ink); border-radius: 2px; }
  .back-brand__name {
    font-weight: 600; font-size: 8px; letter-spacing: .4px;
    text-transform: uppercase; color: var(--ink);
  }
</style>
</head>
<body>
<main class="stage">
  <section class="card card--front" aria-label="Business card front">
    <div class="edge-bar edge-bar--left"></div>
    <div class="edge-bar edge-bar--right"></div>

    <div class="brand">
      <span class="brand__square"></span>
      <span class="brand__name">Cedar Ridge Mechanical</span>
    </div>

    <div class="divider"></div>

    <div class="contact">
      <p class="contact__name"><span class="contact__first">Marta</span> <span class="contact__last">Kovell</span></p>
      <p class="contact__title">Founder &amp; CEO</p>
      <ul class="contact__list">
        <li class="contact__item">
          <svg viewBox="0 0 24 24" fill="#fff"><path d="M6.6 10.8a15.1 15.1 0 0 0 6.6 6.6l2.2-2.2c.3-.3.7-.4 1-.2 1.1.4 2.3.6 3.6.6.6 0 1 .4 1 1V20c0 .6-.4 1-1 1A17 17 0 0 1 3 4c0-.6.4-1 1-1h3.5c.6 0 1 .4 1 1 0 1.3.2 2.5.6 3.6.1.3 0 .7-.2 1z"/></svg>
          (604) 555-0142
        </li>
        <li class="contact__item">
          <svg viewBox="0 0 24 24" fill="none" stroke="#fff" stroke-width="2"><rect x="3" y="5" width="18" height="14" rx="1"/><path d="M3 6l9 7 9-7"/></svg>
          info@cedarridgemech.com
        </li>
        <li class="contact__item">
          <svg viewBox="0 0 24 24" fill="none" stroke="#fff" stroke-width="2"><circle cx="12" cy="12" r="9"/><path d="M3 12h18M12 3c3 3.5 3 14.5 0 18M12 3c-3 3.5-3 14.5 0 18"/></svg>
          www.cedarridgemech.com
        </li>
      </ul>
    </div>

    <p class="address">1840 Harbor Rd. Suite 310 Vancouver, WA 98660</p>
  </section>

  <section class="card card--back" aria-label="Business card back">
    <div class="pattern" role="img" aria-label="Repeating tone-on-tone embossed brand mark pattern"></div>
    <div class="back-brand">
      <span class="back-brand__square"></span>
      <span class="back-brand__name">Cedar Ridge Mechanical</span>
    </div>
  </section>
</main>
</body>
</html>
```